WTF!!! We need a modern professional website for a business litigation law firm.

We need a modern, clean, professional and uncomplicated website for a new business trial and litigation law firm called "Haverlock Trial Firm PLLC". Website must be mobile optimized for iPad and smartphone. The law firm specializes in counseling and representing large corporations, small businesses and entrepreneurs in and out of the courtroom. Lawyers in the firm serve as Florida counsel and trial counsel to organizations facing claims involving product liability, premises liability, professional liability, vehicle and transportation liability, warranty claims, construction defects and delay claims, complex business disputes, commercial litigation and bid disputes in State and Federal Courts. The website is mainly to provide information about the firm, and should include sections describing the firm, identifying the Industries Served and Areas of Practice ," a separate page identifying the "Professionals", a separate page for "Resources & Advisories," and a traveling "Connect With Us" button a site visitor can click on that will launch an email to the Firm's general email account. The website should allow us to easily modify the content on these pages, and let us add/modify links to external information sources. We will not sell anything or take payments through the website. We do need to be able to easily upload and update photographs of attorneys and add new attorneys names/email hyperlinks as the firm grows. We would like to add developments in the law or success stories easily and quickly, such as through a blog page. On the "Connect With Us" page the website should have hyperlinks to email the Firm, and there should be hyperlinks to email each professional on the "Professionals" page. The website should be viewable on mobile devices without distortion. The law firm focuses on trial work and should have some imagery associated with courtrooms, but the overall theme of the site should be modern, clean, and communicate sophistication and strength. The website should be made in Wordpress. We have uploaded logo files for Haverlock Trial Firm.

Target Market(s)

Corporations and companies that are looking for legal representation. Other attorneys/legal industry.

Industry/Entity Type

Legal Industry

Coding

Coded - Design and coding required

Number of Pages Required

1 page

Font styles to use
Sans Serif

Requirements
Must have
• Simple, clean, sophisticated, modern website that includes the logo, watermark of logo, and the elements described above.
Nice to have
• Pictures of city scape, buildings, courtroom, team members.

```html
<!DOCTYPE html>
<html lang="en">
<head>
<meta charset="utf-8">
<title>Haverlock Trial Firm PLLC</title>
<link rel="stylesheet" href="https://fonts.googleapis.com/css2?family=Poppins:ital,wght@0,400;0,500;0,600;0,700;0,800;1,800&family=Lato:wght@400;700&display=swap">
<style>
:root{
  --orange:#f4472b;
  --orange-dark:#d9361c;
  --ink:#1b1b1b;
  --text:#444;
  --muted:#777;
  --dark:#2c2c2c;
  --black:#080808;
  --white:#fff;
  --line:#8a8a8a;
}
*{box-sizing:border-box;margin:0;padding:0}
html,body{width:1200px;height:4785px;overflow:hidden}
body{position:relative;font-family:'Poppins',sans-serif;color:var(--text);background:var(--white)}
.abs{position:absolute}
a{color:inherit;text-decoration:none}
.btn{position:absolute;display:flex;align-items:center;justify-content:center;background:var(--orange);color:var(--white);font-weight:700;font-size:14px;letter-spacing:.3px;text-transform:uppercase}
.section-title{position:absolute;left:0;width:1200px;text-align:center;font-weight:600;font-size:36px;letter-spacing:.5px}
.section-sub{position:absolute;left:0;width:1200px;text-align:center;font-size:11px;letter-spacing:2px;font-weight:500}

/* header / hero */
.hero{position:absolute;left:0;top:0;width:1200px;height:641px;overflow:hidden}
.hero-photo{position:absolute;inset:0;background:linear-gradient(180deg,#3b5a9c 0%,#8a5ea6 22%,#d77a6a 42%,#e9955a 52%,#5b4a5a 68%,#2d3a2a 85%,#253022 100%)}
.hero-shade{position:absolute;inset:0;background:linear-gradient(90deg,rgba(20,20,40,.55) 0%,rgba(20,20,40,.15) 55%,rgba(0,0,0,0) 100%)}
.topbar-cta{position:absolute;left:585px;top:0;width:223px;height:37px;background:var(--orange);color:var(--white);font-weight:600;font-size:14px;display:flex;align-items:center;justify-content:center;clip-path:polygon(0 0,100% 0,100% 100%,12% 100%)}
.topbar-contact{position:absolute;left:808px;top:0;width:392px;height:37px;background:var(--white);display:flex;align-items:center;padding-left:18px;font-size:11px;font-weight:500;color:var(--ink)}
.topbar-contact strong{font-size:18px;font-weight:600;margin-left:8px}
.brand{position:absolute;left:111px;top:54px;color:var(--white);font-weight:700;text-align:center;line-height:1}
.brand .name{font-size:22px;letter-spacing:.5px}
.brand .tag{font-size:9px;letter-spacing:3px;margin-top:4px}
.nav{position:absolute;left:395px;top:56px;display:flex;gap:32px;font-size:11.5px;color:var(--white);font-weight:500;text-transform:uppercase}
.nav .active{font-weight:700;position:relative}
.nav .active::after{content:"";position:absolute;left:50%;top:22px;width:4px;height:4px;border-radius:50%;background:var(--white);transform:translateX(-50%)}
.hero-kicker{position:absolute;left:111px;top:216px;color:var(--white);font-size:20px;letter-spacing:2px;font-weight:400}
.hero-title{position:absolute;left:108px;top:248px;color:var(--white);font-size:62px;font-weight:800;font-style:italic;letter-spacing:.5px}
.hero-text{position:absolute;left:111px;top:330px;width:410px;color:var(--white);font-size:15px;line-height:26px;font-weight:500}
.down-btn{position:absolute;left:579px;top:557px;width:38px;height:38px;border-radius:50%;background:var(--white);border:2px solid var(--orange);display:flex;align-items:center;justify-content:center}

/* about */
.about-photo{position:absolute;left:111px;top:738px;width:428px;height:436px;background:linear-gradient(160deg,#c9a27a 0%,#a98764 40%,#6d5a4a 100%);clip-path:polygon(0 0,100% 0,100% 100%,10% 100%)}
.about-title{position:absolute;left:598px;top:750px;font-size:34px;font-weight:600;color:var(--ink)}
.about-sub{position:absolute;left:600px;top:802px;font-size:11px;letter-spacing:1.5px;color:var(--ink)}
.about-text{position:absolute;left:600px;top:830px;width:500px;font-size:14px;line-height:25.8px;color:var(--text)}

/* practice */
.practice{position:absolute;left:0;top:1241px;width:1200px;height:658px;background:linear-gradient(180deg,#3a3a3a,#262626 70%,#1e1e1e);overflow:hidden}
.practice-cols{position:absolute;inset:0;background:repeating-linear-gradient(90deg,rgba(255,255,255,.04) 0 18px,rgba(0,0,0,.08) 18px 40px)}
.card{position:absolute;top:1527px;width:298px;height:275px;background:rgba(40,40,40,.82);border:2px solid #6d6d6d;color:var(--white);text-align:center;padding-top:26px}
.card svg.icon{display:block;margin:0 auto}
.card h3{font-size:17px;font-weight:600;margin-top:20px;letter-spacing:.3px}
.card p{font-size:13px;line-height:26px;color:#ddd;margin:12px 26px 0}
.card .go{display:block;margin:12px auto 0}
.slide-arrow{position:absolute;top:1652px;width:24px;height:24px;border-radius:50%}

/* industries */
.ind-title{position:absolute;left:108px;top:2008px;font-size:38px;font-weight:600;color:var(--ink)}
.ind-sub{position:absolute;left:111px;top:2063px;font-size:11px;letter-spacing:1px;color:var(--ink)}
.ind-text{position:absolute;left:111px;top:2100px;width:570px;font-size:14px;line-height:25px}
.ind-lead{position:absolute;left:111px;top:2166px;font-size:18px;font-weight:500;color:var(--ink)}
.ind-item{position:absolute;left:111px;width:560px;height:80px}
.ind-item .gem{position:absolute;left:0;top:2px;width:76px;height:76px}
.ind-item h4{position:absolute;left:95px;top:0;font-size:13.5px;font-weight:600;color:var(--ink);text-transform:uppercase}
.ind-item p{position:absolute;left:95px;top:22px;width:460px;font-size:12.5px;line-height:20px}

/* stories */
.stories{position:absolute;left:0;top:2635px;width:1200px;height:746px;background:linear-gradient(180deg,#2a2a2a,#171717);overflow:hidden}
.story-photo{position:absolute;top:2911px;width:312px;height:235px}
.story-date{position:absolute;top:3166px;font-size:11px;color:var(--orange);padding-left:14px;border-left:3px solid var(--orange);line-height:14px}
.story-title{position:absolute;top:3196px;width:300px;font-size:16.5px;line-height:27px;font-weight:600;color:var(--white);padding-left:16px}
.story-more{position:absolute;top:3268px;font-size:13px;font-weight:600;color:var(--white);padding-left:16px}

/* testimonial */
.t-name{position:absolute;left:0;top:3760px;width:1200px;text-align:center;font-size:19px;font-weight:600;color:var(--ink)}
.t-country{position:absolute;left:0;top:3800px;width:1200px;text-align:center;font-size:11px;color:var(--muted)}
.t-stars{position:absolute;left:0;top:3828px;width:1200px;text-align:center;font-size:28px;color:#f5b41e;letter-spacing:1px}
.t-quote{position:absolute;left:270px;top:3872px;width:660px;text-align:center;font-family:'Lato',sans-serif;font-size:15px;line-height:26px;color:#555}
.dots{position:absolute;left:551px;top:3982px;display:flex;gap:8px}
.dots span{width:13px;height:13px;border-radius:50%;background:#d3daf0}
.dots span.on{background:var(--orange)}

/* footer */
.footer{position:absolute;left:0;top:4080px;width:1200px;height:705px;background:var(--black);color:var(--white)}
.f-brand{position:absolute;left:0;top:4240px;width:1200px;text-align:center;line-height:1}
.f-brand .name{font-size:44px;font-weight:700;letter-spacing:1px}
.f-brand .tag{font-size:20px;font-weight:700;letter-spacing:5px;margin-top:6px}
.f-nav{position:absolute;left:0;top:4412px;width:1200px;display:flex;justify-content:center;gap:42px;font-size:15px;font-weight:500;text-transform:uppercase}
.f-contact{position:absolute;left:111px;top:4474px;width:978px;height:113px;border:2px solid #6a6a6a;display:flex}
.f-contact .col{flex:1;display:flex;align-items:flex-start;padding:30px 0 0 20px;gap:14px;border-right:1px solid #444}
.f-contact .col:last-child{border-right:0}
.f-contact .ic{width:40px;height:40px;border-radius:50%;background:var(--orange);display:flex;align-items:center;justify-content:center;flex:none}
.f-contact h5{font-size:14px;font-weight:500;text-transform:uppercase}
.f-contact p{font-family:'Lato',sans-serif;font-size:14px;line-height:21px;margin-top:2px}
.f-links{position:absolute;left:0;top:4628px;width:1200px;display:flex;justify-content:center;gap:38px;font-size:15px}
.f-copy{position:absolute;left:0;top:4700px;width:1200px;text-align:center;font-size:15px}
</style>
</head>
<body>

<!-- Hero -->
<header class="hero">
  <div class="hero-photo" role="img" aria-label="City skyline at sunset with palm trees and highways"></div>
  <div class="hero-shade"></div>
  <svg class="abs" style="left:0;top:0" width="1200" height="641" viewBox="0 0 1200 641">
    <polygon points="0,641 0,560 720,590 1200,641" fill="#fff"/>
    <polygon points="720,574 1200,545 1200,641" fill="var(--orange)"/>
  </svg>
  <a class="topbar-cta" href="mailto:info@haverlocktrial.com">CONNECT WITH US</a>
  <div class="topbar-contact">CONTACT US TODAY: <strong>+1 555 014 2200</strong></div>
  <div class="brand"><div class="name">HAVERLOCK</div><div class="tag">TRIAL FIRM</div></div>
  <nav class="nav">
    <a class="active">Home</a><a>About</a><a>Industries</a><a>Practice Areas</a><a>Resources &amp; Advisories</a><a>Professionals</a>
  </nav>
  <div class="hero-kicker">TRIAL FIRM</div>
  <h1 class="hero-title">WE WIN FOR YOU</h1>
  <p class="hero-text">Lorem ipsum dolor sit amet, consectetur adipiscing elit, sed do eiusmod tempor incididunt ut labore et dolore magna aliqua.</p>
  <a class="btn" style="left:111px;top:431px;width:294px;height:43px;clip-path:polygon(0 0,100% 0,96% 100%,0 100%)">Request a Free Consultation</a>
  <div class="down-btn"><svg width="16" height="16" viewBox="0 0 16 16"><path d="M8 2v11M3 8l5 5 5-5" stroke="var(--orange)" stroke-width="2" fill="none"/></svg></div>
</header>

<!-- About -->
<section>
  <div class="about-photo" role="img" aria-label="Portrait of a smiling attorney in a suit in an office"></div>
  <h2 class="about-title">ABOUT HAVERLOCK TRIAL FIRM</h2>
  <div class="about-sub">WHO WE ARE</div>
  <p class="about-text">Lorem ipsum dolor sit amet, consectetur adipiscing elit, sed do eiusmod tempor incididunt ut labore et dolore magna Duis aute irure dolor in reprehenderit in voluptate velit esse cillum dolore eu fugiat nulla pariatur. Excepteur sint occaecat cupid atat non proint, sunt in culpa qui officia deserunt mollit anm id est aliqua. Ut enim ad minim veniam, quis nostrud exerc iatn ullamco laboris nisi ut aliquip ex ea commodo conse quat. Dui aute irure dolor in eiusm cat cupiat officia deseruntod tempor incididunt ut labore et dolore magna Duisrepreh enderit in voluptate velit esse cillum dolore eu fugiat nulla pariatur. Excepteur sint occaecat cupiat officia deserunt mollit anim id est laborum.</p>
  <a class="btn" style="left:600px;top:1128px;width:142px;height:47px;clip-path:polygon(0 0,100% 0,96% 100%,0 100%)">Read More</a>
</section>

<!-- Practice Areas -->
<section class="practice">
  <div class="practice-cols" role="img" aria-label="Courthouse columns in dark tones"></div>
</section>
<svg class="abs" style="left:0;top:1241px" width="1200" height="140" viewBox="0 0 1200 140">
  <polygon points="0,0 1200,0 1200,14 0,134" fill="#fff"/>
  <polygon points="1200,10 1200,22 0,142 0,130" fill="#111"/>
  <polygon points="0,0 490,82 0,130" fill="var(--orange)"/>
</svg>
<h2 class="section-title" style="top:1413px;color:#fff">PRACTICE AREAS</h2>
<div class="section-sub" style="top:1472px;color:#ddd">WHAT WE OFFER</div>

<div class="slide-arrow" style="left:44px;background:#666;opacity:.6">
  <svg width="24" height="24" viewBox="0 0 24 24"><path d="M15 12H8M11 8l-4 4 4 4" stroke="#222" stroke-width="2" fill="none"/></svg></div>
<div class="slide-arrow" style="left:1134px;background:#fff">
  <svg width="24" height="24" viewBox="0 0 24 24"><path d="M8 12h8M13 8l4 4-4 4" stroke="#222" stroke-width="2" fill="none"/></svg></div>

<article class="card" style="left:111px">
  <svg class="icon" width="56" height="56" viewBox="0 0 56 56" fill="none" stroke="#fff" stroke-width="2"><path d="M8 18l20-10 20 10-20 10z"/><path d="M8 18v20l20 10V28M48 18v10"/><circle cx="42" cy="40" r="9"/><path d="M38 40l3 3 5-5"/></svg>
  <h3>PRODUCT LIABILITY</h3>
  <p>Excepteur sint occaecat cupidatat non proident, sunt in culpa qui officia deserunt</p>
  <svg class="go" width="16" height="16" viewBox="0 0 16 16"><circle cx="8" cy="8" r="8" fill="#fff"/><path d="M5 8h6M8.5 5l3 3-3 3" stroke="#222" stroke-width="1.6" fill="none"/></svg>
</article>
<article class="card" style="left:450px">
  <svg class="icon" width="56" height="56" viewBox="0 0 56 56" fill="none" stroke="#fff" stroke-width="2"><path d="M28 6l14 5v10c0 9-6 15-14 18-8-3-14-9-14-18V11z"/><path d="M22 21l5 5 8-8"/><path d="M4 34l10 8c3 2 6 4 10 4h8M52 34l-10 8c-3 2-6 4-10 4"/></svg>
  <h3>PREMISES LIABILITY</h3>
  <p>Excepteur sint occaecat cupidatat non proident, sunt in culpa qui officia deserunt</p>
  <svg class="go" width="16" height="16" viewBox="0 0 16 16"><circle cx="8" cy="8" r="8" fill="#fff"/><path d="M5 8h6M8.5 5l3 3-3 3" stroke="#222" stroke-width="1.6" fill="none"/></svg>
</article>
<article class="card" style="left:790px">
  <svg class="icon" width="56" height="56" viewBox="0 0 56 56" fill="none" stroke="#fff" stroke-width="2"><circle cx="34" cy="12" r="6"/><path d="M24 50V32c0-6 4-10 10-10s10 4 10 10v18"/><path d="M18 24l10 4v10c0 6-4 10-10 12-6-2-10-6-10-12V28z"/></svg>
  <h3>PROFESSIONAL LIABILITY</h3>
  <p>Excepteur sint occaecat cupidatat non proident, sunt in culpa qui officia deserunt</p>
  <svg class="go" width="16" height="16" viewBox="0 0 16 16"><circle cx="8" cy="8" r="8" fill="#fff"/><path d="M5 8h6M8.5 5l3 3-3 3" stroke="#222" stroke-width="1.6" fill="none"/></svg>
</article>

<!-- Industries -->
<section>
  <h2 class="ind-title">INDUSTRIES WE SERVED</h2>
  <div class="ind-sub">HAVERLOCK TRIAL FIRM PLLC</div>
  <p class="ind-text">Lorem ipsum dolor sit amet, consectetur adipiscing elit, sed do eiusmod si ut aliquip ex ea commodo consequat eu fugiat nulla pariatur.</p>
  <div class="ind-lead">The Law Firm Specializes in</div>

  <div class="ind-item" style="top:2216px">
    <svg class="gem" viewBox="0 0 76 76"><rect x="14" y="14" width="48" height="48" transform="rotate(45 38 38)" fill="var(--orange)"/><g stroke="#fff" stroke-width="2" fill="none"><rect x="29" y="30" width="18" height="16"/><path d="M33 30v-4h10v4M29 38h18"/></g></svg>
    <h4>Counseling and representing large corporations</h4>
    <p>Duis aute irure dolor in reprehenderit in voluptate velit esse cillum dolore eu fugiat nulla pariatur.</p>
  </div>
  <div class="ind-item" style="top:2312px">
    <svg class="gem" viewBox="0 0 76 76"><rect x="14" y="14" width="48" height="48" transform="rotate(45 38 38)" fill="var(--orange)"/><g stroke="#fff" stroke-width="2" fill="none"><path d="M28 30h20l-2 6H30zM30 36v12h16V36M35 48v-6h6v6"/></g></svg>
    <h4>Small businesses and entrepreneurs</h4>
    <p>Duis aute irure dolor in reprehenderit in voluptate velit esse cillum dolore eu fugiat nulla pariatur.</p>
  </div>
  <div class="ind-item" style="top:2416px">
    <svg class="gem" viewBox="0 0 76 76"><rect x="14" y="14" width="48" height="48" transform="rotate(45 38 38)" fill="var(--orange)"/><g stroke="#fff" stroke-width="2" fill="none"><path d="M30 32l8-6 8 6M34 32l8 8M28 48h20M32 44h12v4H32z"/></g></svg>
    <h4>Out of the courtroom</h4>
    <p>Duis aute irure dolor in reprehenderit in voluptate velit esse cillum dolore eu fugiat nulla pariatur.</p>
  </div>
  <a class="btn" style="left:111px;top:2522px;width:295px;height:44px;clip-path:polygon(0 0,100% 0,96% 100%,0 100%)">Request a Free Consultation</a>

  <svg class="abs" style="left:700px;top:1965px" width="500" height="620" viewBox="700 1965 500 620">
    <defs>
      <linearGradient id="g-ind1" x1="0" y1="0" x2="0" y2="1"><stop offset="0" stop-color="#d9c2a7"/><stop offset="1" stop-color="#4c6a90"/></linearGradient>
      <linearGradient id="g-ind2" x1="0" y1="0" x2="1" y2="1"><stop offset="0" stop-color="#e6e1d8"/><stop offset="1" stop-color="#6b5c4e"/></linearGradient>
      <linearGradient id="g-ind3" x1="0" y1="0" x2="1" y2="1"><stop offset="0" stop-color="#b7d2ea"/><stop offset="1" stop-color="#2c4f78"/></linearGradient>
      <linearGradient id="g-ind4" x1="0" y1="0" x2="1" y2="1"><stop offset="0" stop-color="#c7ccd2"/><stop offset="1" stop-color="#2f3540"/></linearGradient>
    </defs>
    <polygon role="img" aria-label="Smiling worker in an apron" points="1013,1975 1138,2100 1013,2225 888,2100" fill="url(#g-ind1)"/>
    <polygon role="img" aria-label="Team meeting in an office" points="862,2160 987,2285 862,2410 737,2285" fill="url(#g-ind2)"/>
    <polygon role="img" aria-label="Glass office towers" points="1164,2160 1289,2285 1164,2410 1039,2285" fill="url(#g-ind3)"/>
    <polygon role="img" aria-label="Business people shaking hands" points="1013,2307 1146,2440 1013,2573 880,2440" fill="url(#g-ind4)"/>
  </svg>
</section>

<!-- Success Stories -->
<section class="stories">
  <div class="practice-cols" role="img" aria-label="Dark courthouse columns"></div>
</section>
<svg class="abs" style="left:0;top:2630px" width="1200" height="150" viewBox="0 0 1200 150">
  <polygon points="0,0 1200,0 1200,145 0,5" fill="#fff"/>
  <polygon points="1200,132 1200,146 0,6 0,0" fill="#111"/>
  <polygon points="710,80 1200,5 1200,130" fill="var(--orange)"/>
</svg>
<h2 class="section-title" style="top:2802px;color:#fff">SUCCESS STORIES</h2>
<div class="section-sub" style="top:2860px;color:#ddd">BLOG</div>

<div class="story-photo" style="left:111px;background:linear-gradient(135deg,#e3e1dc,#8b8377 60%,#3c3a38)" role="img" aria-label="Colleagues reviewing work at a laptop"></div>
<div class="story-photo" style="left:444px;background:linear-gradient(180deg,#3f7fd0 0%,#a7c6e8 40%,#c9c4b8 70%,#7a7266)" role="img" aria-label="Courthouse columns under a blue sky"></div>
<div class="story-photo" style="left:777px;background:linear-gradient(135deg,#ece7df,#c8b59a 55%,#8a6b4a)" role="img" aria-label="Hands signing a document on a desk"></div>

<div class="story-date" style="left:111px">18 Jan 2024</div>
<div class="story-date" style="left:444px">15 Jan 2024</div>
<div class="story-date" style="left:777px">12 Jan 2024</div>
<h3 class="story-title" style="left:111px">Lorem ipsum dolor sit amet, con sectetur adipiscing elit</h3>
<h3 class="story-title" style="left:444px">Lorem ipsum dolor sit amet, con sectetur adipiscing elit</h3>
<h3 class="story-title" style="left:777px">Lorem ipsum dolor sit amet, con sectetur adipiscing elit</h3>
<a class="story-more" style="left:111px">LEARN MORE</a>
<a class="story-more" style="left:444px">LEARN MORE</a>
<a class="story-more" style="left:777px">LEARN MORE</a>

<!-- Testimonials -->
<section>
  <h2 class="section-title" style="top:3488px;color:var(--ink)">WHAT CUSTOMER SAYS</h2>
  <div class="section-sub" style="top:3546px;color:var(--ink)">TESTIMONIALS</div>
  <svg class="abs" style="left:0;top:3580px" width="1200" height="400" viewBox="0 3580 1200 400">
    <circle cx="600" cy="3669" r="69" fill="#fff" stroke="var(--orange)" stroke-width="3"/>
    <circle role="img" aria-label="Client portrait" cx="600" cy="3669" r="60" fill="#e9b48a"/>
    <circle role="img" aria-label="Client portrait" cx="171" cy="3720" r="34" fill="#d9b59c"/>
    <circle role="img" aria-label="Client portrait" cx="1040" cy="3638" r="22" fill="#9a8f88"/>
    <circle cx="388" cy="3731" r="7" fill="var(--orange)"/>
    <circle cx="901" cy="3692" r="3" fill="#111"/>
    <text x="165" y="3880" font-family="Georgia,serif" font-size="170" fill="#d8d8d8">“</text>
    <text x="950" y="3980" font-family="Georgia,serif" font-size="170" fill="#d8d8d8">”</text>
  </svg>
  <div class="t-name">DANIEL CORVETTI</div>
  <div class="t-country">United States</div>
  <div class="t-stars">★★★★★</div>
  <p class="t-quote">Temporibus aaut rerum necessitatibus saepe eveniet ut et voluptates repudiandae sint et molestiae non recusandae. Itaque earum rerum hic tenetur a sapiente delectus, ut aut reiciendis voluptatibus maiores alias consequatur aut perferendis doloribus asperiores repellat.</p>
  <div class="dots"><span></span><span></span><span></span><span class="on"></span><span></span><span></span></div>
</section>

<!-- Footer -->
<footer class="footer"></footer>
<svg class="abs" style="left:0;top:4020px" width="1200" height="140" viewBox="0 0 1200 140">
  <polygon points="0,0 1200,0 1200,60 0,135" fill="#fff"/>
  <polygon points="0,0 490,110 0,132" fill="var(--orange)"/>
</svg>
<div class="f-brand" style="color:#fff"><div class="name">HAVERLOCK</div><div class="tag">TRIAL FIRM</div></div>
<nav class="f-nav" style="color:#fff"><a>Home</a><a>About</a><a>Industries</a><a>Practice Areas</a><a>Resources &amp; Advisories</a><a>Professionals</a></nav>
<div class="f-contact" style="color:#fff">
  <div class="col"><span class="ic"><svg width="18" height="18" viewBox="0 0 18 18"><path d="M9 1a6 6 0 0 0-6 6c0 5 6 10 6 10s6-5 6-10a6 6 0 0 0-6-6z" fill="none" stroke="#fff" stroke-width="1.8"/><circle cx="9" cy="7" r="2" fill="#fff"/></svg></span><div><h5>Address</h5><p>Haverlock Trial Firm<br>PLLC, US</p></div></div>
  <div class="col"><span class="ic"><svg width="18" height="18" viewBox="0 0 18 18"><path d="M4 2l3 3-2 2c1 2 3 4 5 5l2-2 3 3-2 3C7 16 2 11 1 5z" fill="#fff"/></svg></span><div><h5>Phone</h5><p>+1 555 014 2200</p></div></div>
  <div class="col"><span class="ic"><svg width="18" height="18" viewBox="0 0 18 18"><rect x="3" y="6" width="12" height="9" fill="none" stroke="#fff" stroke-width="1.8"/><path d="M5 6V2h8v4M6 10h6M6 12h6" stroke="#fff" stroke-width="1.5"/></svg></span><div><h5>Fax</h5><p>+1 555 014 2201</p></div></div>
  <div class="col"><span class="ic"><svg width="18" height="18" viewBox="0 0 18 18"><rect x="2" y="4" width="14" height="10" fill="none" stroke="#fff" stroke-width="1.8"/><path d="M2 4l7 6 7-6" fill="none" stroke="#fff" stroke-width="1.8"/></svg></span><div><h5>Email</h5><p>info@haverlocktrial.com</p></div></div>
</div>
<div class="f-links" style="color:#fff"><a>Privacy Policy</a><span>|</span><a>Terms &amp; Conditions</a><span>|</span><a>Support Links</a><span>|</span><a>Contact Us</a></div>
<div class="f-copy" style="color:#fff">Copyrights@2025.Haverlock Trial Firm PLLC.All Rights Reserverd</div>

</body>
</html>
```